Business Card Design Project

We are a construction company in Orange County, CA. We need a two sided business card. We would like the back to be our logo with web URL. Front should included Name, title, address, phone, fax and email address.

our address is
627 West Dorrance Blvd, Suite 308
Anaheim, CA 92718

Our logo files are attached.

Construction

```html
<!DOCTYPE html>
<html lang="en">
<head>
<meta charset="utf-8">
<title>Ridgeway Business Card</title>
<link href="https://fonts.googleapis.com/css2?family=Open+Sans:wght@400;700&display=swap" rel="stylesheet">
<style>
  :root {
    --backdrop: #e7e3de;
    --card: #ffffff;
    --brand-blue: #164a7e;
    --ink: #3d3d3d;
    --rule-dark: #222222;
  }
  * { margin: 0; padding: 0; box-sizing: border-box; }
  html, body { width: 1200px; height: 1099px; overflow: hidden; }
  body {
    position: relative;
    background: var(--backdrop);
    font-family: "Open Sans", Arial, sans-serif;
    color: var(--ink);
  }
  .card {
    position: absolute;
    background: var(--card);
    border-radius: 30px;
    overflow: hidden;
  }
  .card-front { left: 76px; top: 79px; width: 790px; height: 450px; }
  .card-back { left: 334px; top: 579px; width: 792px; height: 452px; }

  .brand-bar {
    position: absolute; left: 0; top: 45px; width: 7px; height: 130px;
    background: var(--brand-blue);
  }
  .info-bar {
    position: absolute; right: 0; top: 181px; width: 8px; height: 224px;
    background: var(--rule-dark);
  }
  .wordmark {
    position: absolute;
    color: var(--brand-blue);
    font-weight: 700;
    letter-spacing: -1px;
    line-height: 1;
    white-space: nowrap;
  }
  .card-front .wordmark { left: 27px; top: 55px; font-size: 84px; }
  .card-back .wordmark { left: 0; right: 0; top: 112px; text-align: center; font-size: 84px; }

  .contact {
    position: absolute; right: 26px; top: 188px;
    text-align: right;
  }
  .contact-name { font-size: 27px; color: var(--brand-blue); line-height: 1; margin-bottom: 20px; }
  .contact-name strong { font-weight: 700; }
  .contact-list { list-style: none; font-size: 19px; line-height: 25.5px; }
  .contact-list li { display: flex; justify-content: flex-end; align-items: center; gap: 7px; }
  .contact-list svg { width: 15px; height: 15px; fill: var(--ink); }
  .address { font-size: 19px; line-height: 24px; margin-top: 15px; }

  .web-address {
    position: absolute; left: 0; right: 0; top: 320px;
    text-align: center; font-size: 26px; letter-spacing: 2px; color: var(--ink);
  }
</style>
</head>
<body>
  <section class="card card-front" aria-label="Card front">
    <div class="brand-bar"></div>
    <div class="wordmark">RIDGEWAY</div>
    <div class="info-bar"></div>
    <div class="contact">
      <p class="contact-name"><strong>Your Name,</strong> Title</p>
      <ul class="contact-list">
        <li><svg viewBox="0 0 16 16" aria-hidden="true"><path d="M4 1l3 3-2 2c1 2 3 4 5 5l2-2 3 3-2 2C7 15 1 9 2 3z"/></svg>01-234-5678</li>
        <li><svg viewBox="0 0 16 16" aria-hidden="true"><path d="M4 2h7v4H4zM1 7h14v6h-2v2h-2v-2H5v2H3v-2H1z"/></svg>01-234-5678</li>
        <li><svg viewBox="0 0 16 16" aria-hidden="true"><path d="M1 4h14v9H1zM2 5l6 4 6-4v-.5H2z" fill-rule="evenodd"/></svg>info@ridgewaybuild.com</li>
        <li><svg viewBox="0 0 16 16" aria-hidden="true"><circle cx="8" cy="8" r="7"/><path d="M1 8h14M8 1c3 3 3 11 0 14M8 1c-3 3-3 11 0 14" stroke="#fff" fill="none"/></svg>www.ridgewaybuild.com</li>
      </ul>
      <p class="address">627 West Dorrance Blvd<br>Suite 308, Anaheim, CA&nbsp; 92718</p>
    </div>
  </section>

  <section class="card card-back" aria-label="Card back">
    <div class="wordmark">RIDGEWAY</div>
    <p class="web-address">www.ridgewaybuild.com</p>
  </section>
</body>
</html>
```